New Business Card for Software Company

We are looking at rebranding a 10 year old company that specializes in PDF and DWF solutions for Architects and Engineers. We will attach the new company logo that we are going with so you can work with that and complimentary colors.
The sample information we would like on the business card is:
Gerald Pinfold
Vice President
4738 W. Harrowgate Lane. STE 305
PMB#417
Mesa, AZ 85374
866-392-5074 US Toll Free
123-456-3190 Cell
gpinfold@plavorix.com
The old tag line that we had on the business cars was.
Providing Industrial Strength PDF and DWF Solutions to the Global CAD Marketplace.
If you have an idea for a better tag line we are open to that also.
Updates
We would like to thank all of the Designers for their wonderful work. We apologize that we will not have the time to provide feedback to everyone. There is just so many innovative and professional designs that you have all created making our decision even harder.
Target Market(s)
Architects and Engineers
Industry/Entity Type
Business
Look and feel

```html
<!DOCTYPE html>
<html lang="en">
<head>
<meta charset="utf-8">
<title>Plavorix Business Card</title>
<link rel="stylesheet" href="https://fonts.googleapis.com/css2?family=Open+Sans:wght@400;600;700&display=swap">
<style>
  :root {
    --page-bg: #ecebe8;
    --card-white: #ffffff;
    --band-grey: #6d6e71;
    --brand-grey: #58595b;
    --brand-orange: #f26a21;
    --deep-red: #d42d2a;
    --warm-orange: #f47b20;
    --light-orange: #f9a03f;
    --text-grey: #4d4d4f;
    --white: #ffffff;
  }
  * { box-sizing: border-box; margin: 0; padding: 0; }
  html, body { width: 1200px; height: 720px; overflow: hidden; }
  body {
    background: var(--page-bg);
    font-family: "Open Sans", Arial, sans-serif;
    position: relative;
  }
  .card {
    position: absolute;
    top: 205px;
    width: 540px;
    height: 309px;
    overflow: hidden;
    box-shadow: 0 6px 18px rgba(0,0,0,0.18);
  }
  .card--front { left: 40px; background: var(--card-white); }
  .card--back {
    left: 620px;
    background: radial-gradient(ellipse at 50% 40%, var(--light-orange) 0%, var(--warm-orange) 45%, var(--deep-red) 115%);
  }
  .card__shapes { position: absolute; inset: 0; width: 100%; height: 100%; }

  .brand {
    position: absolute;
    left: 34px;
    top: 92px;
    display: flex;
    align-items: center;
    gap: 12px;
  }
  .brand__dot {
    width: 44px; height: 44px; border-radius: 50%;
    background: var(--brand-orange);
  }
  .brand__name {
    font-weight: 700;
    font-size: 46px;
    letter-spacing: -1px;
    color: var(--brand-grey);
    line-height: 1;
  }

  .person { position: absolute; left: 34px; top: 190px; }
  .person__name { font-weight: 700; font-size: 15px; color: var(--brand-orange); }
  .person__title { font-size: 11px; color: var(--text-grey); margin-top: 1px; }
  .person__address { font-size: 12px; color: var(--text-grey); margin-top: 14px; line-height: 1.4; }

  .contact {
    position: absolute;
    right: 22px;
    top: 126px;
    list-style: none;
    color: var(--white);
    font-size: 11.5px;
  }
  .contact__item { display: flex; align-items: center; gap: 6px; margin-bottom: 7px; justify-content: flex-end; }
  .contact__icon { width: 11px; height: 11px; flex: none; }

  .back-brand {
    position: absolute;
    left: 0; right: 0; top: 92px;
    display: flex; align-items: center; justify-content: center; gap: 14px;
  }
  .back-brand__dot { width: 70px; height: 70px; border-radius: 50%; background: var(--light-orange); }
  .back-brand__name { font-weight: 700; font-size: 44px; color: var(--white); letter-spacing: -1px; }

  .tagline {
    position: absolute;
    left: 0; right: 0; bottom: 38px;
    text-align: center;
    color: var(--white);
    font-size: 15px;
    line-height: 1.4;
  }
</style>
</head>
<body>
  <section class="card card--front" aria-label="Business card front">
    <svg class="card__shapes" viewBox="0 0 540 309" preserveAspectRatio="none" aria-hidden="true">
      <defs>
        <linearGradient id="front-sweep" x1="0" y1="1" x2="1" y2="0">
          <stop offset="0" stop-color="#f7941d"/>
          <stop offset="0.5" stop-color="#f26a21"/>
          <stop offset="1" stop-color="#d42d2a"/>
        </linearGradient>
      </defs>
      <path d="M380 0 C430 60 420 200 180 309 L540 309 L540 0 Z" fill="var(--band-grey)"/>
      <path d="M412 0 C462 70 450 210 220 309 L540 309 L540 0 Z" fill="url(#front-sweep)"/>
    </svg>

    <div class="brand">
      <span class="brand__dot"></span>
      <span class="brand__name">plavorix</span>
    </div>

    <div class="person">
      <p class="person__name">Gerald Pinfold</p>
      <p class="person__title">Vice President</p>
      <p class="person__address">4738 W. Harrowgate Lane. STE 305<br>PMB#417, Mesa, AZ 85374</p>
    </div>

    <ul class="contact">
      <li class="contact__item">
        <svg class="contact__icon" viewBox="0 0 12 12" aria-hidden="true"><circle cx="6" cy="6" r="5.5" fill="none" stroke="#fff"/><path d="M4 3.5 L5 3.5 L5.5 5 L4.8 5.6 Q5.6 7 6.5 7.3 L7.1 6.6 L8.5 7.1 L8.5 8.1 Q5 8.5 3.6 4.2 Z" fill="#fff"/></svg>
        866-392-5074 US(TF)
      </li>
      <li class="contact__item">
        <svg class="contact__icon" viewBox="0 0 12 12" aria-hidden="true"><rect x="3" y="0.5" width="6" height="11" rx="1" fill="#fff"/><rect x="4" y="2" width="4" height="6" fill="#f26a21"/></svg>
        123-456-3190
      </li>
      <li class="contact__item">
        <svg class="contact__icon" viewBox="0 0 12 12" aria-hidden="true"><rect x="0.5" y="2.5" width="11" height="7" fill="#fff"/><path d="M0.5 2.5 L6 6.5 L11.5 2.5" fill="none" stroke="#e2512a"/></svg>
        gpinfold@plavorix.com
      </li>
    </ul>
  </section>

  <section class="card card--back" aria-label="Business card back">
    <div class="back-brand">
      <span class="back-brand__dot"></span>
      <span class="back-brand__name">plavorix</span>
    </div>
    <p class="tagline">Providing Industrial Strength PDF and<br>DWF Solutions to the Global CAD Marketplace</p>
  </section>
</body>
</html>
```